The Vantor Codex Book Cover

"The Vantor Codex" is a book I wrote with the slogan "Unlock Performance, Spark Engagement: Master the Art of Building Winning Cultures in Today's Hybrid World". The book is designed around a methodology that's mine and that I attached. I would love to see the graphic of the methodology integrated in the design in a very subtle way. Use colors from the model but the book cover should be catchy, modern and engaging to the eye.
Overall the book is about three key elements towards success:
- (Self) Directions (purpose)
- Human experience (people and psychological safety)
- Maximize engagement
The methodology is a FLOW so flow is something that could be incorporated as well in the concept.
Low design quality
Managers and Teams

```html
<!DOCTYPE html>
<html lang="en">
<head>
<meta charset="utf-8">
<title>The Vantor Codex — Book Cover</title>
<link rel="stylesheet" href="https://fonts.googleapis.com/css2?family=Bebas+Neue&family=Cinzel:wght@400;500&family=Oswald:wght@600&display=swap">
<style>
  :root {
    --ink: #000000;
    --paper: #ffffff;
    --flow-violet: #8a86f0;
    --flow-amber: #e0a850;
    --flow-teal: #58c4dc;
    --flow-green: #7fc070;
    --flow-red: #c0304a;
  }
  html, body {
    margin: 0;
    padding: 0;
    width: 934px;
    height: 1200px;
    overflow: hidden;
    background: var(--ink);
  }
  .cover {
    position: relative;
    width: 934px;
    height: 1200px;
    background: var(--ink);
    color: var(--paper);
    overflow: hidden;
  }
  .author {
    position: absolute;
    top: 66px;
    left: 0;
    width: 100%;
    text-align: center;
    font-family: "Cinzel", serif;
    font-weight: 400;
    font-size: 52px;
    letter-spacing: 2px;
    line-height: 1;
    margin: 0;
  }
  .title {
    position: absolute;
    top: 200px;
    left: 0;
    width: 100%;
    margin: 0;
    text-align: center;
    font-family: "Bebas Neue", sans-serif;
    font-weight: 400;
    line-height: 1;
  }
  .title-lead {
    display: block;
    font-size: 84px;
    letter-spacing: 1px;
  }
  .title-main {
    display: block;
    margin-top: -2px;
    font-size: 146px;
    letter-spacing: 2px;
  }
  .tagline {
    position: absolute;
    top: 413px;
    left: 221px;
    width: 484px;
    height: 40px;
    border-top: 3px solid var(--paper);
    border-bottom: 3px solid var(--paper);
    box-sizing: border-box;
    display: flex;
    align-items: center;
    justify-content: center;
    font-family: "Oswald", sans-serif;
    font-weight: 600;
    font-size: 12px;
    letter-spacing: 7.4px;
    text-transform: uppercase;
    white-space: nowrap;
    margin: 0;
  }
  .subtitle {
    position: absolute;
    top: 466px;
    left: 0;
    width: 100%;
    text-align: center;
    font-family: "Cinzel", serif;
    font-weight: 500;
    font-size: 17px;
    line-height: 21px;
    letter-spacing: 0.4px;
    margin: 0;
  }
  .flow-art {
    position: absolute;
    left: 60px;
    top: 628px;
    width: 760px;
    height: 445px;
    background:
      radial-gradient(ellipse 28% 42% at 22% 62%, rgba(224,168,80,0.55), transparent 70%),
      radial-gradient(ellipse 30% 30% at 30% 22%, rgba(138,134,240,0.55), transparent 70%),
      radial-gradient(ellipse 22% 30% at 50% 55%, rgba(88,196,220,0.45), transparent 70%),
      radial-gradient(ellipse 26% 30% at 72% 30%, rgba(127,192,112,0.45), transparent 70%),
      radial-gradient(ellipse 22% 34% at 80% 72%, rgba(88,196,220,0.55), transparent 70%),
      radial-gradient(ellipse 8% 12% at 48% 32%, rgba(192,48,74,0.4), transparent 70%);
    filter: blur(6px);
  }
  .editor {
    position: absolute;
    top: 1088px;
    left: 0;
    width: 100%;
    text-align: center;
    font-family: "Cinzel", serif;
    font-weight: 400;
    font-size: 57px;
    letter-spacing: 2px;
    line-height: 1;
    margin: 0;
  }
</style>
</head>
<body>
  <main class="cover">
    <p class="author">AUTHOR NAME</p>
    <h1 class="title">
      <span class="title-lead">THE VANTOR</span>
      <span class="title-main">CODEX</span>
    </h1>
    <p class="tagline">Unlock Performance, Spark Engagement:</p>
    <p class="subtitle">Master the Art of Building Winning Cultures<br>in Today's Hybrid World</p>
    <div class="flow-art" role="img" aria-label="Glowing multicoloured light-trail ribbon forming an infinity loop, in violet, amber, teal and green, symbolising continuous flow"></div>
    <p class="editor">EDITOR</p>
  </main>
</body>
</html>
```